Black card, Logo on front, in brushed silver, embossed or stamped
details centred on the back of the card written in Serif Old type face
Hotel
Red Heron Hotel Motel (or smaller logo)
your hosts
Brendan and Corina Walsh
left bottom:
7 Halvorn Street
Kellbrook NSW 2741
right bottom:
P: 02 61738495
M: 0438 512 764
W: www.redheronhotel.com.au
E: redheronhotel@mailvista.com
facebook emblem: @RedHeronHotel
instagram emblem: @redheronhotel

```html
<!DOCTYPE html>
<html lang="en">
<head>
<meta charset="utf-8">
<title>Red Heron Hotel Motel — Business Card</title>
<link rel="stylesheet" href="https://fonts.googleapis.com/css2?family=EB+Garamond:wght@500;600;700&display=swap">
<style>
  :root {
    --backdrop: #2b2b2b;
    --card: #050505;
    --silver-light: #e6e6e6;
    --silver-mid: #a9a9a9;
    --silver-dark: #5c5c5c;
    --ink: #f2f2f2;
    --muted: #7d7d7d;
    --rule: #bdbdbd;
  }
  * { margin: 0; padding: 0; box-sizing: border-box; }
  html, body {
    width: 1200px; height: 900px; overflow: hidden;
    background: var(--backdrop);
    font-family: "EB Garamond", Georgia, serif;
  }
  .canvas { position: relative; width: 1200px; height: 900px; }

  .card {
    position: absolute;
    width: 560px; height: 320px;
    background: var(--card);
    box-shadow: 0 18px 40px rgba(0,0,0,.55);
  }
  .card--front { left: 100px; top: 110px; }
  .card--back  { left: 540px; top: 470px; }

  /* front */
  .front-mark {
    position: absolute; left: 0; right: 0; top: 92px;
    display: flex; flex-direction: column; align-items: center; gap: 18px;
  }
  .bird-art {
    width: 110px; height: 70px; border-radius: 4px;
    background: linear-gradient(135deg, var(--silver-mid), var(--silver-dark));
  }
  .brand-name {
    font-size: 34px; font-weight: 600; letter-spacing: 1px;
    color: var(--silver-mid);
  }

  /* back */
  .back-art {
    position: absolute; left: 95px; top: 100px;
    width: 190px; height: 135px; border-radius: 4px;
    background: linear-gradient(135deg, var(--silver-light), var(--silver-dark));
  }
  .back-divider {
    position: absolute; left: 318px; top: 52px;
    width: 1px; height: 190px; background: var(--rule);
  }
  .contact {
    position: absolute; left: 334px; top: 46px;
    color: var(--ink); font-weight: 600;
    font-size: 14px; line-height: 19px;
  }
  .contact__hosts { font-size: 19px; font-weight: 700; line-height: 24px; }
  .contact__role { color: var(--muted); font-size: 15px; margin-bottom: 2px; }
  .contact__line { display: flex; align-items: center; gap: 7px; }
  .contact__line svg { width: 11px; height: 11px; flex: none; }

  .social {
    position: absolute; left: 0; right: 0; bottom: 36px;
    display: flex; align-items: center; justify-content: center; gap: 14px;
    color: var(--ink); font-size: 16px; font-weight: 600;
  }
  .social__rule { height: 1px; background: var(--rule); width: 92px; }
  .social__item { display: flex; align-items: center; gap: 6px; }
  .social__dot { width: 11px; height: 11px; background: var(--silver-mid); border-radius: 2px; }
</style>
</head>
<body>
<main class="canvas">

  <section class="card card--front" aria-label="Card front">
    <div class="front-mark">
      <div class="bird-art" role="img" aria-label="Brushed silver bird in flight illustration"></div>
      <div class="brand-name">Red Heron Hotel Motel</div>
    </div>
  </section>

  <section class="card card--back" aria-label="Card back">
    <div class="back-art" role="img" aria-label="Large brushed silver bird in flight illustration"></div>
    <div class="back-divider"></div>

    <div class="contact">
      <div class="contact__hosts">Brendan &amp; Corina Walsh</div>
      <div class="contact__role">Your Hosts</div>
      <div class="contact__line">7 Halvorn Street</div>
      <div class="contact__line">Kellbrook NSW 2741</div>
      <div class="contact__line">
        <svg viewBox="0 0 12 12" aria-hidden="true"><path d="M3 1l2 2.5-1.2 1.2c.6 1.3 1.4 2.1 2.6 2.6L7.6 6 10 8l-1 2C5 10 2 7 2 3z" fill="none" stroke="var(--silver-mid)" stroke-width="1.1"/></svg>
        02 61738495
      </div>
      <div class="contact__line">
        <svg viewBox="0 0 12 12" aria-hidden="true"><rect x="3" y="1" width="6" height="10" rx="1" fill="none" stroke="var(--silver-mid)" stroke-width="1.1"/><circle cx="6" cy="9.2" r=".6" fill="var(--silver-mid)"/></svg>
        0438 512 764
      </div>
      <div class="contact__line">
        <svg viewBox="0 0 12 12" aria-hidden="true"><circle cx="6" cy="6" r="2" fill="none" stroke="var(--silver-mid)" stroke-width="1.1"/><path d="M8 4v2.8c0 1 1.8 1 1.8-.8A3.8 3.8 0 1 0 7.5 9.5" fill="none" stroke="var(--silver-mid)" stroke-width="1.1"/></svg>
        redheronhotel@mailvista.com
      </div>
      <div class="contact__line">
        <svg viewBox="0 0 12 12" aria-hidden="true"><circle cx="6" cy="6" r="4.8" fill="none" stroke="var(--silver-mid)" stroke-width="1.1"/><ellipse cx="6" cy="6" rx="2" ry="4.8" fill="none" stroke="var(--silver-mid)" stroke-width="1"/><path d="M1.2 6h9.6" stroke="var(--silver-mid)" stroke-width="1"/></svg>
        www.redheronhotel.com.au
      </div>
    </div>

    <div class="social">
      <span class="social__rule"></span>
      <span class="social__item"><span class="social__dot"></span>@RedHeronHotel</span>
      <span class="social__item"><span class="social__dot"></span>@redheronhotel</span>
      <span class="social__rule"></span>
    </div>
  </section>

</main>
</body>
</html>
```